Online Dating Website called WinkAtWheel.com

PLEASE CAN ALL PARTICIPATING DESIGNERS PLEASE SUBMIT ALL PAGES AS DETAILED IN THE ORIGINAL BRIEF BELOW WITHIN 48 HOURS TO AVOID WINKATWHEEL EXTENDING THE CONTEST FURTHER.

We have an online dating website that is 95% fully functional and now require an exciting and creative designer to help us create the best dating experience. We are looking for your ideas on a couple of our key pages. These are our landing, profile and search page. We already have a homepage that we are happy with and winning designers will look to build upon the foundations of the homepage and extend them through their designs.

The premise of the site is the idea that if you've ever seen someone out driving and wished you could communicate because you found them attractive, how would you? Well with WinkAtWheel.com you can. Just enter their vehicle registration number (license plate) in to the website in order to get in touch, flirt and develop a relationship. It also allows users to find each other based on other criteria. It acts as both a specialist service and a normal dating website.

The pages that require developing are 1) our landing page, this is the page users see when they first login to the site, it comprises various pieces of information but it's primary function is a live feed of events generated based on the users favourited profiles and interactions with the user. 2) The profile page is the page where users can edit their own information, given the nature of this page we are looking for a creative design that gives this page some flair. 3) Finally we are looking for ideas for our search page, this page needs to provide a list of users who meet the user's search requirements and display the profile of a selected user.
Updates

Project Deadline Extended
Reason: We've asked for certain pages in our brief to be designed and this still hasn't been done. We've contacted the designers that have currently submitted designs and requested this several times. We still await for this to happen.

Target Market(s)

Male or Female age 18+

Industry/Entity Type

Dating

Requirements
Must have
• Our must have feature is a designer with an open mind. The functionality of the site must be present, all we ask is for you to be creative with the layout. Think out side of the box, change the colours, the layout, and the background as you feel. Make it look current and appealing to the user.
Nice to have
• Theme's carried through from the home page
Should not have
• Do not include Comic Sans or Times New Roman font in your designs.

```html
<!DOCTYPE html>
<html lang="en">
<head>
<meta charset="utf-8">
<title>WinkAtWheel – Live Feed</title>
<link rel="stylesheet" href="https://fonts.googleapis.com/css2?family=Open+Sans:wght@400;600;700&display=swap">
<style>
:root{
  --night:#1b1020;
  --pink:#ec4c9a;
  --pink-soft:#f26aa9;
  --blue:#2c9ce8;
  --sky:#3ba7ef;
  --panel-dark:#49494d;
  --ink:#1d1d1f;
  --text:#5b5b5f;
  --muted:#8b8b90;
  --line:#e4e4e6;
  --tile:#f3f3f4;
  --white:#ffffff;
}
*{box-sizing:border-box;margin:0;padding:0}
html,body{width:1076px;height:1200px;overflow:hidden}
body{position:relative;font-family:"Open Sans",Arial,sans-serif;color:var(--text);
  background:radial-gradient(ellipse at 35% 30%,#8a1c8a 0%,transparent 45%),
    radial-gradient(ellipse at 90% 55%,#c2246e 0%,transparent 40%),
    radial-gradient(ellipse at 10% 85%,#5a1466 0%,transparent 45%),
    linear-gradient(160deg,#2a0d36 0%,#4a1250 45%,#2b0a2c 100%)}
.site-header{position:absolute;left:0;top:0;width:1076px;height:61px;background:var(--night);border-bottom:1px solid #3a2a40}
.brand{position:absolute;left:26px;top:12px;display:flex;align-items:center;gap:10px;color:var(--white);font-size:30px;font-weight:400;letter-spacing:-.5px}
.brand-dot{width:22px;height:22px;border-radius:50%;background:var(--pink)}
.main-nav{position:absolute;left:488px;top:22px;display:flex;gap:0;font-size:14px}
.main-nav a{color:#b4acb8;text-decoration:none;margin-right:32px}
.main-nav a.support{color:var(--sky);display:flex;gap:6px;align-items:center;margin-right:20px}
.main-nav a.account{color:var(--pink);display:flex;gap:6px;align-items:center;margin-right:0}
.plate-search{position:absolute;left:43px;top:88px;width:664px;height:96px;background:var(--panel-dark);border-radius:4px 0 0 4px}
.plate-search h2{position:absolute;left:17px;top:10px;color:var(--white);font-size:20px;font-weight:700}
.field{position:absolute;top:42px;height:39px;background:var(--white);border-radius:2px;display:flex;align-items:center;justify-content:space-between;padding:0 12px;font-size:16px;color:#8c8c90}
.field.reg{left:17px;width:228px}
.field.make{left:256px;width:139px}
.field.colour{left:406px;width:138px}
.btn-search{position:absolute;left:555px;top:42px;width:90px;height:39px;background:var(--blue);color:var(--white);font-weight:700;font-size:14px;display:flex;align-items:center;justify-content:center;border-radius:2px}
.welcome{position:absolute;left:707px;top:88px;width:324px;height:96px;background:var(--blue);border-radius:0 4px 4px 0;color:var(--white);font-size:20px;line-height:25px;padding:10px 20px 0 47px}
.member-card{position:absolute;left:25px;top:221px;width:147px;height:634px;background:var(--white);box-shadow:0 2px 6px rgba(0,0,0,.35);z-index:2}
.member-top{background:var(--pink-soft);height:288px;padding:8px 9px 0}
.member-photo{width:128px;height:143px;background:radial-gradient(circle at 50% 40%,#b8896a 0%,#5a3a2a 50%,#1d1512 100%)}
.member-name{color:var(--white);font-weight:700;font-size:16px;margin-top:6px}
.member-meta{color:var(--white);font-size:11px;line-height:17px;font-weight:600}
.card-btn{margin-top:6px;height:25px;background:#f4f4f5;border-radius:2px;display:flex;align-items:center;gap:12px;padding-left:10px;font-size:12px;font-weight:700;color:#6a6a6e;letter-spacing:.3px}
.card-btn:first-of-type{margin-top:10px}
.side-section{padding:10px 9px 0}
.side-title{color:var(--sky);font-weight:600;font-size:13px;margin-bottom:7px}
.filter-list{list-style:none;font-size:12px;color:#555;border-bottom:1px solid var(--line);padding-bottom:8px}
.filter-list li{height:24px;display:flex;justify-content:space-between;align-items:center}
.swatches{display:grid;grid-template-columns:repeat(3,39px);gap:6px 5px}
.swatch{height:27px;border-radius:2px}
.feed-panel{position:absolute;left:161px;top:210px;width:890px;height:888px;background:var(--white)}
.status-box{position:absolute;left:21px;top:11px;width:422px;height:38px;border:1px solid #dcdcde;font-size:14px;color:#6a6a6e;padding:9px 12px}
.btn-update{position:absolute;left:449px;top:11px;width:79px;height:38px;border:1px solid #dcdcde;background:#f7f7f8;font-size:13px;font-weight:600;color:#8a8a8e;display:flex;align-items:center;justify-content:center}
.stats{position:absolute;left:537px;top:0;width:353px;height:60px;background:#c7c7c9;display:flex;gap:6px;padding:10px}
.stat{flex:1;background:var(--white);display:flex;align-items:center;gap:8px;padding-left:8px;font-size:13px;line-height:14px;color:#666}
.stat b{display:block;color:var(--ink);font-size:14px}
.feed{position:absolute;left:32px;top:79px;width:579px}
.post{height:133px;border-top:2px solid var(--pink);background:linear-gradient(#f1f1f2 0,#fff 48px);position:relative;padding:14px 14px 0}
.post-head{display:flex;gap:10px}
.avatar{background:radial-gradient(circle at 50% 40%,#d6a88a 0%,#8a5a40 55%,#2c2a3a 100%);flex:none}
.post-avatar{width:52px;height:52px}
.post-title{color:var(--ink);font-weight:600;font-size:15px;margin-top:2px}
.post-time{display:flex;gap:14px;font-size:10px;color:var(--muted);margin-top:6px;align-items:center}
.post-time span{display:flex;gap:5px;align-items:center}
.post-body{font-size:11.5px;line-height:20px;color:#555;margin-top:10px}
.like-btn{position:absolute;right:14px;top:12px;width:24px;height:20px;background:#f4f4f5;border:1px solid #e0e0e2;border-radius:2px;display:flex;align-items:center;justify-content:center}
.aside{position:absolute;left:649px;top:85px;width:221px}
.aside h3{color:var(--sky);font-size:13px;font-weight:600;padding-bottom:6px;border-bottom:1px solid var(--line)}
.name-search{margin:11px 0 6px;height:29px;border:2px solid #e6e6e8;display:flex;align-items:center;justify-content:space-between;padding:0 8px;font-size:14px;color:#666}
.fav{display:flex;gap:12px;height:65px;padding-top:4px}
.fav-avatar{width:50px;height:50px;background:radial-gradient(circle at 50% 45%,#d9a68a 0%,#7a3e28 55%,#3d1f14 100%)}
.fav-info{font-size:12px;line-height:16px;color:#777}
.fav-info b{color:var(--ink);font-size:13px;display:block;margin-bottom:3px}
.matches-title{margin-top:8px}
.match-list{list-style:none;margin-top:10px;font-size:12px;color:#555;line-height:14px}
.match-list li{display:flex;gap:12px;margin-bottom:13px}
.match-list b{color:var(--ink)}
.match-grid{margin-top:10px;background:var(--tile);padding:14px 15px 8px;display:grid;grid-template-columns:repeat(3,50px);justify-content:space-between;row-gap:10px;margin-left:1px;width:220px}
.match-grid figure{text-align:center;font-size:12px;font-weight:600;color:#444}
.match-grid .fav-avatar{margin-bottom:2px}
.chat-btn{position:absolute;left:934px;top:1167px;width:117px;height:33px;background:var(--blue);border-radius:3px 3px 0 0;color:var(--white);font-size:12px;font-weight:700;display:flex;align-items:center;justify-content:center;gap:8px}
</style>
</head>
<body>
<header class="site-header">
  <div class="brand">winkatwheel<span class="brand-dot"></span></div>
  <nav class="main-nav">
    <a>Home</a><a>Profile</a><a>Message</a><a>Matches</a><a>Search</a>
    <a class="support"><svg width="14" height="14" viewBox="0 0 14 14"><path d="M2 8V7a5 5 0 0 1 10 0v1" fill="none" stroke="currentColor" stroke-width="1.6"/><rect x="1" y="7" width="3" height="5" rx="1" fill="currentColor"/><rect x="10" y="7" width="3" height="5" rx="1" fill="currentColor"/></svg>Support</a>
    <a class="account"><svg width="13" height="14" viewBox="0 0 13 14"><circle cx="6.5" cy="4" r="3.5" fill="currentColor"/><path d="M0 14a6.5 6 0 0 1 13 0z" fill="currentColor"/></svg>My Account</a>
  </nav>
</header>

<section class="plate-search">
  <h2>SEEN Someone?</h2>
  <div class="field reg">Search REG<svg width="16" height="16" viewBox="0 0 16 16"><circle cx="6.5" cy="6.5" r="5" fill="none" stroke="#ec4c9a" stroke-width="2"/><path d="M10 10l5 5" stroke="#ec4c9a" stroke-width="2.2"/></svg></div>
  <div class="field make">Make<svg width="12" height="10" viewBox="0 0 12 10"><path d="M0 0h12L6 10z" fill="#ec4c9a"/></svg></div>
  <div class="field colour">Colour<svg width="12" height="10" viewBox="0 0 12 10"><path d="M0 0h12L6 10z" fill="#ec4c9a"/></svg></div>
  <div class="btn-search">SEARCH</div>
</section>
<aside class="welcome">Welcome, Our site is currently free during beta testing.</aside>

<aside class="member-card">
  <div class="member-top">
    <div class="member-photo" role="img" aria-label="Member profile photo"></div>
    <div class="member-name">Linda</div>
    <div class="member-meta">Age: 19 years old<br>From: Wakefield</div>
    <div class="card-btn"><svg width="10" height="11" viewBox="0 0 10 11"><circle cx="5" cy="3" r="3" fill="#ec4c9a"/><path d="M0 11a5 5 0 0 1 10 0z" fill="#ec4c9a"/></svg>PROFILE</div>
    <div class="card-btn"><svg width="10" height="11" viewBox="0 0 10 11"><path d="M5 0l5 5H7v6H3V5H0z" fill="#ec4c9a"/></svg>UPLOAD</div>
  </div>
  <div class="side-section">
    <div class="side-title">Feed Filter</div>
    <ul class="filter-list">
      <li>Status Updates<svg width="6" height="10" viewBox="0 0 6 10"><path d="M1 1l4 4-4 4" fill="none" stroke="#aaa"/></svg></li>
      <li>Image Uploads<svg width="6" height="10" viewBox="0 0 6 10"><path d="M1 1l4 4-4 4" fill="none" stroke="#aaa"/></svg></li>
      <li>Profile Updates<svg width="6" height="10" viewBox="0 0 6 10"><path d="M1 1l4 4-4 4" fill="none" stroke="#aaa"/></svg></li>
      <li>Others<svg width="6" height="10" viewBox="0 0 6 10"><path d="M1 1l4 4-4 4" fill="none" stroke="#aaa"/></svg></li>
    </ul>
  </div>
  <div class="side-section">
    <div class="side-title">Select Background</div>
    <div class="swatches">
      <div class="swatch" role="img" aria-label="Background option: soft green" style="background:#9cc27a"></div>
      <div class="swatch" role="img" aria-label="Background option: green beans" style="background:#4e7a2a"></div>
      <div class="swatch" role="img" aria-label="Background option: candles" style="background:#8a4a22"></div>
      <div class="swatch" role="img" aria-label="Background option: pebbles" style="background:#5b5a48"></div>
      <div class="swatch" role="img" aria-label="Background option: wood" style="background:#9a5e2e"></div>
      <div class="swatch" role="img" aria-label="Background option: grey stones" style="background:#6f6f72"></div>
      <div class="swatch" role="img" aria-label="Background option: sand" style="background:#a78a62"></div>
      <div class="swatch" role="img" aria-label="Background option: night sky" style="background:#2c3e6a"></div>
      <div class="swatch" role="img" aria-label="Background option: mountains" style="background:#6b6f66"></div>
      <div class="swatch" role="img" aria-label="Background option: golden field" style="background:#c99a4e"></div>
      <div class="swatch" role="img" aria-label="Background option: crowd" style="background:#5a3a3a"></div>
      <div class="swatch" role="img" aria-label="Background option: purple sunset" style="background:#6a4a6e"></div>
      <div class="swatch" role="img" aria-label="Background option: light blue" style="background:#7cc0e8"></div>
      <div class="swatch" role="img" aria-label="Background option: candles" style="background:#7a3a20"></div>
      <div class="swatch" role="img" aria-label="Background option: green beans" style="background:#4a7a28"></div>
    </div>
  </div>
</aside>

<main class="feed-panel">
  <div class="status-box">How are you?</div>
  <div class="btn-update">UPDATE</div>
  <div class="stats">
    <div class="stat"><svg width="20" height="18" viewBox="0 0 20 18"><path d="M10 18L1.5 9.5A5 5 0 0 1 10 3a5 5 0 0 1 8.5 6.5z" fill="#ec4c9a"/></svg><div><b>124</b>Likes</div></div>
    <div class="stat"><svg width="20" height="14" viewBox="0 0 20 14"><rect width="20" height="14" fill="#ec4c9a"/><path d="M0 0l10 8 10-8" fill="none" stroke="#fff" stroke-width="1.5"/></svg><div><b>171</b>Messages</div></div>
    <div class="stat"><svg width="20" height="19" viewBox="0 0 20 19"><path d="M10 0l3 6.5 7 .8-5.2 4.8 1.4 6.9L10 15.5 3.8 19l1.4-6.9L0 7.3l7-.8z" fill="#ec4c9a"/></svg><div><b>20</b>Favourites</div></div>
  </div>

  <div class="feed">
    <article class="post"><div class="post-head"><div class="avatar post-avatar" role="img" aria-label="Mike's profile photo"></div><div><div class="post-title">Mike changed his status</div><div class="post-time"><span><svg width="9" height="9" viewBox="0 0 9 9"><rect x=".5" y="1.5" width="8" height="7" fill="none" stroke="#888"/><path d="M.5 3.5h8" stroke="#888"/></svg>Tuesday</span><span><svg width="10" height="10" viewBox="0 0 10 10"><circle cx="5" cy="5" r="4" fill="none" stroke="#888"/><path d="M5 2.5V5h2" fill="none" stroke="#888"/></svg>22:56</span></div></div></div><p class="post-body">This is Pixelforge's version &nbsp;of Lorem Ipsum. Proin gravida nibh vel velit auctor aliquet. Aenean sollicitudin, lorem quis bibendum auctor, nisi elit consequat ipsum, nec sagittis sem nibh id elit.</p><div class="like-btn"><svg width="12" height="11" viewBox="0 0 20 18"><path d="M10 18L1.5 9.5A5 5 0 0 1 10 3a5 5 0 0 1 8.5 6.5z" fill="#b8b8bc"/></svg></div></article>
    <article class="post"><div class="post-head"><div class="avatar post-avatar" role="img" aria-label="Mike's profile photo"></div><div><div class="post-title">Mike changed his status</div><div class="post-time"><span><svg width="9" height="9" viewBox="0 0 9 9"><rect x=".5" y="1.5" width="8" height="7" fill="none" stroke="#888"/><path d="M.5 3.5h8" stroke="#888"/></svg>Tuesday</span><span><svg width="10" height="10" viewBox="0 0 10 10"><circle cx="5" cy="5" r="4" fill="none" stroke="#888"/><path d="M5 2.5V5h2" fill="none" stroke="#888"/></svg>22:56</span></div></div></div><p class="post-body">This is Pixelforge's version &nbsp;of Lorem Ipsum. Proin gravida nibh vel velit auctor aliquet. Aenean sollicitudin, lorem quis bibendum auctor, nisi elit consequat ipsum, nec sagittis sem nibh id elit.</p><div class="like-btn"><svg width="12" height="11" viewBox="0 0 20 18"><path d="M10 18L1.5 9.5A5 5 0 0 1 10 3a5 5 0 0 1 8.5 6.5z" fill="#b8b8bc"/></svg></div></article>
    <article class="post"><div class="post-head"><div class="avatar post-avatar" role="img" aria-label="Mike's profile photo"></div><div><div class="post-title">Mike changed his status</div><div class="post-time"><span><svg width="9" height="9" viewBox="0 0 9 9"><rect x=".5" y="1.5" width="8" height="7" fill="none" stroke="#888"/><path d="M.5 3.5h8" stroke="#888"/></svg>Tuesday</span><span><svg width="10" height="10" viewBox="0 0 10 10"><circle cx="5" cy="5" r="4" fill="none" stroke="#888"/><path d="M5 2.5V5h2" fill="none" stroke="#888"/></svg>22:56</span></div></div></div><p class="post-body">This is Pixelforge's version &nbsp;of Lorem Ipsum. Proin gravida nibh vel velit auctor aliquet. Aenean sollicitudin, lorem quis bibendum auctor, nisi elit consequat ipsum, nec sagittis sem nibh id elit.</p><div class="like-btn"><svg width="12" height="11" viewBox="0 0 20 18"><path d="M10 18L1.5 9.5A5 5 0 0 1 10 3a5 5 0 0 1 8.5 6.5z" fill="#b8b8bc"/></svg></div></article>
    <article class="post"><div class="post-head"><div class="avatar post-avatar" role="img" aria-label="Mike's profile photo"></div><div><div class="post-title">Mike changed his status</div><div class="post-time"><span><svg width="9" height="9" viewBox="0 0 9 9"><rect x=".5" y="1.5" width="8" height="7" fill="none" stroke="#888"/><path d="M.5 3.5h8" stroke="#888"/></svg>Tuesday</span><span><svg width="10" height="10" viewBox="0 0 10 10"><circle cx="5" cy="5" r="4" fill="none" stroke="#888"/><path d="M5 2.5V5h2" fill="none" stroke="#888"/></svg>22:56</span></div></div></div><p class="post-body">This is Pixelforge's version &nbsp;of Lorem Ipsum. Proin gravida nibh vel velit auctor aliquet. Aenean sollicitudin, lorem quis bibendum auctor, nisi elit consequat ipsum, nec sagittis sem nibh id elit.</p><div class="like-btn"><svg width="12" height="11" viewBox="0 0 20 18"><path d="M10 18L1.5 9.5A5 5 0 0 1 10 3a5 5 0 0 1 8.5 6.5z" fill="#b8b8bc"/></svg></div></article>
    <article class="post"><div class="post-head"><div class="avatar post-avatar" role="img" aria-label="Mike's profile photo"></div><div><div class="post-title">Mike changed his status</div><div class="post-time"><span><svg width="9" height="9" viewBox="0 0 9 9"><rect x=".5" y="1.5" width="8" height="7" fill="none" stroke="#888"/><path d="M.5 3.5h8" stroke="#888"/></svg>Tuesday</span><span><svg width="10" height="10" viewBox="0 0 10 10"><circle cx="5" cy="5" r="4" fill="none" stroke="#888"/><path d="M5 2.5V5h2" fill="none" stroke="#888"/></svg>22:56</span></div></div></div><p class="post-body">This is Pixelforge's version &nbsp;of Lorem Ipsum. Proin gravida nibh vel velit auctor aliquet. Aenean sollicitudin, lorem quis bibendum auctor, nisi elit consequat ipsum, nec sagittis sem nibh id elit.</p><div class="like-btn"><svg width="12" height="11" viewBox="0 0 20 18"><path d="M10 18L1.5 9.5A5 5 0 0 1 10 3a5 5 0 0 1 8.5 6.5z" fill="#b8b8bc"/></svg></div></article>
    <article class="post"><div class="post-head"><div class="avatar post-avatar" role="img" aria-label="Mike's profile photo"></div><div><div class="post-title">Mike changed his status</div><div class="post-time"><span><svg width="9" height="9" viewBox="0 0 9 9"><rect x=".5" y="1.5" width="8" height="7" fill="none" stroke="#888"/><path d="M.5 3.5h8" stroke="#888"/></svg>Tuesday</span><span><svg width="10" height="10" viewBox="0 0 10 10"><circle cx="5" cy="5" r="4" fill="none" stroke="#888"/><path d="M5 2.5V5h2" fill="none" stroke="#888"/></svg>22:56</span></div></div></div><p class="post-body">This is Pixelforge's version &nbsp;of Lorem Ipsum. Proin gravida nibh vel velit auctor aliquet. Aenean sollicitudin, lorem quis bibendum auctor, nisi elit consequat ipsum, nec sagittis sem nibh id elit.</p><div class="like-btn"><svg width="12" height="11" viewBox="0 0 20 18"><path d="M10 18L1.5 9.5A5 5 0 0 1 10 3a5 5 0 0 1 8.5 6.5z" fill="#b8b8bc"/></svg></div></article>
  </div>

  <div class="aside">
    <h3>Your Favourites</h3>
    <div class="name-search">Type a name<svg width="16" height="16" viewBox="0 0 16 16"><circle cx="6.5" cy="6.5" r="5" fill="none" stroke="#ec4c9a" stroke-width="2"/><path d="M10 10l5 5" stroke="#ec4c9a" stroke-width="2.2"/></svg></div>
    <div class="fav"><div class="fav-avatar" role="img" aria-label="Jenny's profile photo"></div><div class="fav-info"><b>jenny</b>19 years old<br>Leeds</div></div>
    <div class="fav"><div class="fav-avatar" role="img" aria-label="Jenny's profile photo"></div><div class="fav-info"><b>jenny</b>19 years old<br>Leeds</div></div>
    <div class="fav"><div class="fav-avatar" role="img" aria-label="Jenny's profile photo"></div><div class="fav-info"><b>jenny</b>19 years old<br>Leeds</div></div>
    <div class="fav"><div class="fav-avatar" role="img" aria-label="Jenny's profile photo"></div><div class="fav-info"><b>jenny</b>19 years old<br>Leeds</div></div>
    <div class="fav"><div class="fav-avatar" role="img" aria-label="Jenny's profile photo"></div><div class="fav-info"><b>jenny</b>19 years old<br>Leeds</div></div>

    <h3 class="matches-title">Your Matches</h3>
    <ul class="match-list">
      <li><svg width="14" height="12" viewBox="0 0 14 12"><rect y="2" width="14" height="10" rx="1" fill="#ec4c9a"/><rect x="4" width="6" height="3" fill="#ec4c9a"/><circle cx="7" cy="7" r="2.5" fill="#fff"/></svg><span><b>WAW</b> has uploaded a new image</span></li>
      <li><svg width="14" height="12" viewBox="0 0 14 12"><rect y="2" width="14" height="10" rx="1" fill="#ec4c9a"/><rect x="4" width="6" height="3" fill="#ec4c9a"/><circle cx="7" cy="7" r="2.5" fill="#fff"/></svg><span><b>Lee</b> has uploaded a new image</span></li>
      <li><svg width="14" height="13" viewBox="0 0 14 13"><path d="M7 0C3 0 0 2.4 0 5.5c0 1.8 1 3.3 2.5 4.3L2 13l3.5-2c.5.1 1 .1 1.5.1 4 0 7-2.5 7-5.6S11 0 7 0z" fill="#ec4c9a"/></svg><span><b>WAW</b> has updated his status</span></li>
      <li><svg width="14" height="13" viewBox="0 0 14 13"><path d="M7 0C3 0 0 2.4 0 5.5c0 1.8 1 3.3 2.5 4.3L2 13l3.5-2c.5.1 1 .1 1.5.1 4 0 7-2.5 7-5.6S11 0 7 0z" fill="#ec4c9a"/></svg><span><b>Lee</b> has updated his status</span></li>
    </ul>
    <div class="match-grid">
      <figure><div class="fav-avatar" role="img" aria-label="Jenny's profile photo"></div>jenny</figure>
      <figure><div class="fav-avatar" role="img" aria-label="Jenny's profile photo"></div>jenny</figure>
      <figure><div class="fav-avatar" role="img" aria-label="Jenny's profile photo"></div>jenny</figure>
      <figure><div class="fav-avatar" role="img" aria-label="Jenny's profile photo"></div>jenny</figure>
      <figure><div class="fav-avatar" role="img" aria-label="Jenny's profile photo"></div>jenny</figure>
      <figure><div class="fav-avatar" role="img" aria-label="Jenny's profile photo"></div>jenny</figure>
    </div>
  </div>
</main>

<div class="chat-btn"><svg width="18" height="15" viewBox="0 0 18 15"><path d="M6 0C2.7 0 0 2 0 4.5c0 1.4.8 2.6 2 3.4L1.5 10l2.8-1.4c.5.1 1.1.2 1.7.2 3.3 0 6-2 6-4.4S9.3 0 6 0z" fill="#fff"/><path d="M13 5c2.8.3 5 2 5 4.2 0 1.2-.6 2.2-1.7 2.9l.4 2-2.4-1.2c-.4.1-.9.1-1.3.1-2.4 0-4.4-1.1-5.2-2.6 3-.4 5.2-2.6 5.2-5.4z" fill="#fff"/></svg>OPEN CHAT</div>
</body>
</html>
```